New Website for World Wide Charity (KOLVAN)

We need a dynamic web design for our brand new charity organisation that will be working worldwide. We will be funded by donations so need to attract people to donate.

What We Do
We work to optimise the wellbeing of the planet, the animals and all that live within. Our slogan is Achieving Vibrational Equilibrium.

We have included a Powerpoint document which may help you understand what we need, it is just an idea for structure and style, it is not set in stone so feel free to be as creative as you like!
Updates

Designs look the same

Target Market(s)

Adults 18+ with an interest in animal, environmental. Businesses that may like to support our natural world or already support our natural world.

Number of Pages Required

3 page

Colors

Designer to choose colors to be used in the design.

Requirements
Must have
• We need the website to be easy to use and understand.

Web pages will be Home, What We Do, Who We Are, Success Stories, What You Can Do (Blog section), Seek Help, Donate, Join.
Nice to have
• Natural feel, easy to navigate, Ideally the website will look natural and organic.

Natural colours, blues, greens, sand, gold, brown, grey, silver, Orange and yellow for impact.
Should not have
• Should not have a dark coloured theme.

```html
<!DOCTYPE html>
<html lang="en">
<head>
<meta charset="utf-8">
<title>KOLVAN – Achieving Vibrational Equilibrium</title>
<link href="https://fonts.googleapis.com/css2?family=Roboto:wght@400;500;700&display=swap" rel="stylesheet">
<style>
:root{
  --green:#2d6a3c;
  --green-dark:#1d4f2c;
  --navy:#223b8c;
  --ink:#333333;
  --text:#555555;
  --footer:#1b1b1c;
  --lilac:#c8a3dc;
  --white:#ffffff;
  --brand:#3d5c9e;
  --ring:#4a6aa8;
}
*{box-sizing:border-box;margin:0;padding:0}
html,body{width:1200px;height:3026px;overflow:hidden}
body{position:relative;font-family:'Roboto',sans-serif;background:var(--white);color:var(--ink)}
.abs{position:absolute}

/* header */
.site-header{position:absolute;left:0;top:0;width:1200px;height:149px;background:var(--white);border-bottom:1px solid #e6e6e6;z-index:3}
.brand-badge{position:absolute;left:111px;top:17px;width:212px;height:212px;border-radius:50%;background:var(--white);box-shadow:inset 0 0 0 14px var(--white),inset 0 0 0 17px var(--ring);z-index:5;display:flex;align-items:center;justify-content:center}
.brand-badge span{font-size:30px;font-weight:500;letter-spacing:2px;color:var(--brand)}
.btn-join{position:absolute;left:966px;top:26px;width:122px;height:47px;border-radius:24px;background:var(--navy);color:var(--white);font-size:16px;font-weight:500;display:flex;align-items:center;justify-content:center}
.main-nav{position:absolute;top:102px;right:111px;display:flex;gap:34px;font-size:13px;font-weight:500;color:var(--ink)}
.main-nav .active{color:var(--green)}

/* hero */
.hero{position:absolute;left:0;top:149px;width:1200px;height:753px}
.hero svg{position:absolute;left:0;top:0}
.hero-title{position:absolute;left:110px;top:210px;font-size:31px;font-weight:500;color:var(--green)}
.hero-sub{position:absolute;left:111px;top:263px;font-size:20px;font-weight:500;color:#2b2b2b}
.btn-primary{position:absolute;left:112px;top:314px;width:193px;height:54px;border-radius:27px;background:var(--green);color:var(--white);font-size:15px;font-weight:500;display:flex;align-items:center;justify-content:center}

/* focus cards */
.focus-card{position:absolute;top:985px;width:310px;height:403px;border-radius:6px;overflow:hidden}
.focus-card .shade{position:absolute;left:0;right:0;bottom:0;height:200px;background:linear-gradient(to bottom,rgba(0,0,0,0),rgba(0,0,0,.7))}
.focus-card h3{position:absolute;left:0;right:0;top:299px;text-align:center;font-size:19px;font-weight:500;color:var(--white)}
.btn-outline{position:absolute;left:50%;top:332px;transform:translateX(-50%);width:129px;height:40px;border:1px solid var(--white);border-radius:20px;color:var(--white);font-size:12px;font-weight:500;display:flex;align-items:center;justify-content:center}

/* feature rows */
.feature-media{position:absolute;width:489px;height:313px}
.feature-copy{position:absolute;width:404px}
.feature-copy h2{font-size:24px;font-weight:500;color:#2b2b2b}
.feature-copy .rule{width:46px;height:3px;background:var(--green);margin:14px 0 24px}
.feature-copy p{font-family:Arial,'Roboto',sans-serif;font-size:13.5px;line-height:25.8px;color:var(--text);text-align:justify}

/* footer */
.site-footer{position:absolute;left:0;top:2490px;width:1200px;height:536px}
.site-footer svg{position:absolute;left:0;top:0}
.footer-col{position:absolute;top:135px;color:var(--white)}
.footer-col h4{font-size:23px;font-weight:500;margin-bottom:24px}
.footer-col li{list-style:none;font-size:15.5px;height:32.7px;color:#e8e8e8}
.footer-col li::before{content:"»";margin-right:16px}
.footer-divider{position:absolute;left:112px;top:339px;width:978px;height:1px;background:#2a2a2a}
.footer-badge{position:absolute;left:120px;top:359px;width:160px;height:160px;border-radius:50%;background:var(--white);box-shadow:inset 0 0 0 10px var(--white),inset 0 0 0 13px var(--ring);display:flex;align-items:center;justify-content:center}
.footer-badge span{font-size:22px;font-weight:500;letter-spacing:1.5px;color:var(--brand)}
.footer-nav{position:absolute;top:401px;right:111px;display:flex;gap:34px;font-size:13px;font-weight:500;color:var(--white)}
.footer-meta{position:absolute;top:464px;left:420px;width:669px;display:flex;justify-content:space-between;font-size:13px;font-weight:500;color:var(--white)}
</style>
</head>
<body>

<header class="site-header">
  <a class="btn-join">JOIN</a>
  <nav class="main-nav">
    <span class="active">HOME</span><span>WHAT WE DO</span><span>WHO WE ARE</span><span>SUCCESS STORIES</span><span>WHAT YOU CAN DO</span><span>DONATE</span>
  </nav>
</header>
<div class="brand-badge"><span>KOLVAN</span></div>

<section class="hero">
  <svg width="1200" height="753" viewBox="0 0 1200 753">
    <defs>
      <clipPath id="heroClip"><path d="M0 0H1200V600Q600 870 0 600Z"/></clipPath>
      <linearGradient id="heroSky" x1="0" y1="0" x2="0" y2="1">
        <stop offset="0" stop-color="#d3ebe6"/>
        <stop offset=".4" stop-color="#dcefd6"/>
        <stop offset=".65" stop-color="#b7d98e"/>
        <stop offset=".85" stop-color="#5f9a3e"/>
        <stop offset="1" stop-color="#2c5e22"/>
      </linearGradient>
      <radialGradient id="heroGlowRight" cx=".72" cy=".45" r=".35">
        <stop offset="0" stop-color="#4f8f3a" stop-opacity=".55"/>
        <stop offset="1" stop-color="#4f8f3a" stop-opacity="0"/>
      </radialGradient>
      <radialGradient id="heroGlowFar" cx=".95" cy=".5" r=".22">
        <stop offset="0" stop-color="#3f7a35" stop-opacity=".5"/>
        <stop offset="1" stop-color="#3f7a35" stop-opacity="0"/>
      </radialGradient>
      <radialGradient id="heroGlowLeft" cx=".22" cy=".8" r=".25">
        <stop offset="0" stop-color="#2f6a32" stop-opacity=".6"/>
        <stop offset="1" stop-color="#2f6a32" stop-opacity="0"/>
      </radialGradient>
      <radialGradient id="heroMist" cx=".25" cy=".3" r=".35">
        <stop offset="0" stop-color="#eef6ee" stop-opacity=".8"/>
        <stop offset="1" stop-color="#eef6ee" stop-opacity="0"/>
      </radialGradient>
    </defs>
    <path d="M0 0H1200V614Q600 892 0 614Z" fill="var(--green-dark)"/>
    <g role="img" aria-label="Children and a bear in forest silhouettes running through a meadow with birds" clip-path="url(#heroClip)">
      <rect width="1200" height="753" fill="url(#heroSky)"/>
      <rect width="1200" height="753" fill="url(#heroGlowRight)"/>
      <rect width="1200" height="753" fill="url(#heroGlowFar)"/>
      <rect width="1200" height="753" fill="url(#heroGlowLeft)"/>
      <rect width="1200" height="753" fill="url(#heroMist)"/>
    </g>
  </svg>
  <h1 class="hero-title">HELP RAISE WORLD VIBRATION</h1>
  <p class="hero-sub">ACHIEVING VIBRATIONAL EQUILIBRIUM</p>
  <a class="btn-primary">MAKE A DIFFERENCE</a>
</section>

<article class="focus-card" style="left:112px">
  <div role="img" aria-label="Sunlit green forest foliage" class="abs" style="inset:0;background:radial-gradient(circle at 25% 15%,rgba(240,235,170,.85),rgba(240,235,170,0) 35%),radial-gradient(circle at 80% 30%,rgba(170,230,200,.6),rgba(170,230,200,0) 40%),radial-gradient(circle at 30% 75%,#3f8a2a,rgba(63,138,42,0) 50%),linear-gradient(165deg,#9fcf78,#4b9a52 40%,#2b6a2e 70%,#143a18)"></div>
  <div class="shade"></div>
  <h3>ENVIRONMENT</h3><a class="btn-outline">FIND OUT MORE</a>
</article>
<article class="focus-card" style="left:446px">
  <div role="img" aria-label="Hummingbird feeding at a purple flower" class="abs" style="inset:0;background:radial-gradient(circle at 92% 10%,rgba(120,140,230,.9),rgba(120,140,230,0) 25%),radial-gradient(ellipse at 50% 62%,rgba(110,120,80,.75),rgba(110,120,80,0) 40%),linear-gradient(170deg,#6a4fc8,#7358c2 45%,#857aa8 70%,#7d8a56)"></div>
  <div class="shade" style="background:linear-gradient(to bottom,rgba(0,0,0,0),rgba(80,90,45,.55))"></div>
  <h3>ANIMAL</h3><a class="btn-outline">FIND OUT MORE</a>
</article>
<article class="focus-card" style="left:780px">
  <div role="img" aria-label="Silhouettes of people holding hands at sunset" class="abs" style="inset:0;background:radial-gradient(ellipse at 80% 62%,rgba(230,170,110,.7),rgba(230,170,110,0) 35%),linear-gradient(180deg,#6b80ab,#8d95b0 35%,#3a3a44 52%,#1f1f26 80%)"></div>
  <div class="shade"></div>
  <h3>HUMAN</h3><a class="btn-outline">FIND OUT MORE</a>
</article>

<div class="feature-media" role="img" aria-label="Wind turbines standing in a green field" style="left:112px;top:1479px;background:radial-gradient(ellipse at 60% 20%,rgba(230,240,240,.8),rgba(230,240,240,0) 40%),radial-gradient(ellipse at 40% 85%,#1f5a1f,rgba(31,90,31,0) 45%),linear-gradient(180deg,#7b9cb0,#b4c6c2 35%,#4d9a45 55%,#2e7a2c 75%,#183f18)"></div>
<div class="feature-copy" style="left:654px;top:1528px">
  <h2>ENVIRONMENT</h2><div class="rule"></div>
  <p>Sed ut perspiciatis unde omnis iste natus error sit voluptatem accus antium doloremque laudantium, totam rem aperiam, eaque ipsa quae ab illo inventore veritatis et quasi architecto beatae vitae dicta sunt explicabo. Nemo enim ipsam voluptatem quia voluptas sit aspernatur aut odit aut fugit, sed quia consequuntur magni dolores eos qui ratione voluptatem sequi nesciunt.</p>
</div>

<div class="feature-copy" style="left:141px;top:1842px">
  <h2>ANIMAL</h2><div class="rule"></div>
  <p>Sed ut perspiciatis unde omnis iste natus error sit voluptatem accus antium doloremque laudantium, totam rem aperiam, eaque ipsa quae ab illo inventore veritatis et quasi architecto beatae vitae dicta sunt explicabo. Nemo enim ipsam voluptatem quia voluptas sit aspernatur aut odit aut fugit, sed quia consequuntur magni dolores eos qui ratione voluptatem sequi nesciunt.</p>
</div>
<div class="feature-media" role="img" aria-label="Brown bear walking through tall grass at a forest edge" style="left:601px;top:1793px;background:radial-gradient(ellipse at 50% 15%,rgba(130,150,90,.6),rgba(130,150,90,0) 35%),radial-gradient(ellipse at 72% 62%,rgba(90,60,30,.7),rgba(90,60,30,0) 18%),linear-gradient(180deg,#26321c,#3f5226 40%,#8f9a3c 62%,#a4a848 75%,#4e6222)"></div>

<div class="feature-media" role="img" aria-label="Line of people holding hands silhouetted against sunset" style="left:112px;top:2106px;background:radial-gradient(ellipse at 85% 70%,rgba(240,160,70,.85),rgba(240,160,70,0) 35%),linear-gradient(180deg,#4a6398,#8f9ab4 35%,#d8a974 58%,#2a2a34 74%,#141418)"></div>
<div class="feature-copy" style="left:654px;top:2154px">
  <h2>HUMAN</h2><div class="rule"></div>
  <p>Sed ut perspiciatis unde omnis iste natus error sit voluptatem accus antium doloremque laudantium, totam rem aperiam, eaque ipsa quae ab illo inventore veritatis et quasi architecto beatae vitae dicta sunt explicabo. Nemo enim ipsam voluptatem quia voluptas sit aspernatur aut odit aut fugit, sed quia consequuntur magni dolores eos qui ratione voluptatem sequi nesciunt.</p>
</div>

<footer class="site-footer">
  <svg width="1200" height="536" viewBox="0 0 1200 536">
    <path d="M0 93Q600 -73 1200 93V536H0Z" fill="var(--lilac)"/>
    <path d="M0 93Q600 -57 1200 93V536H0Z" fill="var(--footer)"/>
  </svg>
  <div class="footer-col" style="left:207px"><h4>GET INVOLVED</h4><ul><li>Join Us</li><li>Fundraise</li><li>Donate</li><li>Shop</li></ul></div>
  <div class="footer-col" style="left:545px"><h4>GET HELP</h4><ul><li>Contact Us</li><li>Media</li></ul></div>
  <div class="footer-col" style="left:858px"><h4>LEGAL</h4><ul><li>Terms and Conditions</li><li>Cookies</li><li>Privacy Policy</li></ul></div>
  <div class="footer-divider"></div>
  <div class="footer-badge"><span>KOLVAN</span></div>
  <nav class="footer-nav"><span>HOME</span><span>WHAT WE DO</span><span>WHO WE ARE</span><span>SUCCESS STORIES</span><span>WHAT YOU CAN DO</span><span>DONATE</span></nav>
  <div class="footer-meta"><span>CHARITY NUMBE : 100200300</span><span>© COPYRIGHTS 2021 KOLVAN. ALL RIGHTS RESERVED</span></div>
</footer>

</body>
</html>
```